Quintel Packaging Business Card

Project Overview
We are seeking a modern, minimalist business card that effectively represents our company while making a bold and lasting impression. The design should reflect trust, professionalism, and innovation, reinforcing our expertise in custom plastic manufacturing for warehouse and distribution centers.

Provided Assets & Specifications
Logo: We will provide our official logo for integration into the design.
Design Files: Photoshop (PSD) files for our printing specifications will be supplied.

Card Size & Material:
Dimensions: 3.5" x 2"
Material: 1/8" Radius Plastic Business Cards with 1/8" Rounded Corners
Clear plastic background—the design should strategically incorporate transparency.
Orientation: The card should be designed in landscape format for a sleek and professional presentation.

Design Requirements:
Logo Prominence
The logo must be the focal point of the card.
Space should be used effectively to draw attention to the logo while maintaining a minimalist layout.

Clear Plastic Integration
The transparent background should create the illusion of blank space, enhancing the modern and high-quality feel.
Avoid any frosted effects—we do not want white areas to appear semi-transparent.

Minimalist & Impactful
Clean, structured, and easy to read at a glance.
Focus on sharp contrast to ensure legibility and visibility.
The design should instill confidence and reflect our role as a leading plastics manufacturer.

Color Palette & Contrast
Primary Colors: Blue, Black, White, and Grey
Use bold black or blue for text and key elements to ensure they stand out against the clear plastic.
Avoid light, pastel, or neon colors that may fade into the plastic background.
No frosted or semi-transparent white—we do not want a cloudy effect.

Typography & Information Hierarchy
Bold, modern typography—clear, professional, and highly legible.
The business card should highlight:
Company Logo (Primary Focus)
Full Name & Title
Phone Number
Email
Website

Brand Representation
The card should reflect our expertise in manufacturing high-quality custom plastics for large-scale packaging and distribution businesses.
Our clients rely on us to enhance their brand presence through custom plastic solutions, and our business cards should reinforce that sense of precision and trust.

Final Considerations
Utilize the clear plastic effectively to differentiate our brand from standard business cards.
Maintain a sleek, professional aesthetic while ensuring all text and elements remain legible.
The design should align with our industry, conveying reliability and innovation.
We look forward to seeing a design that captures our brand identity, maximizes the clear plastic medium, and makes a strong, professional impact on our clients.

```html
<!DOCTYPE html>
<html lang="en">
<head>
<meta charset="utf-8">
<title>Quintel Packaging Business Card</title>
<link href="https://fonts.googleapis.com/css2?family=Lato:wght@400;700;900&display=swap" rel="stylesheet">
<style>
  :root {
    --backdrop: #2a2a2a;
    --card-dark: #3c3c3c;
    --ink-dark: #0c0c0c;
    --card-light: #ffffff;
    --ink: #2e2e2e;
    --brand-blue: #0a87c0;
  }
  * { margin: 0; padding: 0; box-sizing: border-box; }
  html, body {
    width: 1200px; height: 689px; overflow: hidden;
    background: var(--backdrop);
    font-family: "Lato", sans-serif;
  }
  .stage {
    width: 1200px; height: 689px;
    display: flex; align-items: center; justify-content: center; gap: 60px;
  }
  .card {
    width: 510px; height: 291px;
    border-radius: 18px;
    position: relative;
    overflow: hidden;
  }
  .card-front {
    background: var(--card-dark);
    display: flex; align-items: center; justify-content: center; gap: 18px;
  }
  .front-mark {
    width: 54px; height: 54px;
    background: var(--ink-dark);
    flex: none;
  }
  .front-wordmark {
    font-weight: 900; font-size: 40px; letter-spacing: 0.5px;
    color: var(--ink-dark);
    white-space: nowrap;
  }
  .card-back { background: var(--card-light); }
  .back-wordmark {
    position: absolute; left: 30px; top: 34px;
    font-weight: 900; font-size: 30px; color: var(--ink);
    letter-spacing: 0.3px; white-space: nowrap;
  }
  .wordmark-rule {
    position: absolute; left: 30px; top: 78px;
    width: 236px; height: 3px; background: var(--brand-blue);
  }
  .back-square {
    position: absolute; right: 34px; top: 50px;
    width: 176px; height: 176px;
    border: 16px solid var(--brand-blue);
  }
  .person { position: absolute; left: 30px; top: 98px; }
  .person-name { font-size: 21px; font-weight: 700; color: var(--ink); letter-spacing: 0.3px; }
  .person-title { font-size: 13px; color: var(--ink); margin-top: 1px; }
  .contact-list {
    position: absolute; left: 30px; top: 160px;
    list-style: none; font-size: 13px; color: var(--ink);
  }
  .contact-item { display: flex; align-items: flex-start; gap: 10px; line-height: 20px; }
  .contact-icon { width: 14px; height: 14px; margin-top: 3px; flex: none; }
  .contact-icon svg { display: block; width: 14px; height: 14px; fill: var(--brand-blue); }
</style>
</head>
<body>
<main class="stage">
  <section class="card card-front" aria-label="Card front">
    <span class="front-mark"></span>
    <span class="front-wordmark">Quintel Packaging</span>
  </section>

  <section class="card card-back" aria-label="Card back">
    <div class="back-wordmark">Quintel Packaging</div>
    <div class="wordmark-rule"></div>
    <div class="back-square"></div>
    <div class="person">
      <div class="person-name">MARCUS HALE</div>
      <div class="person-title">Owner</div>
    </div>
    <ul class="contact-list">
      <li class="contact-item">
        <span class="contact-icon"><svg viewBox="0 0 16 16"><path d="M3.5 1.5l2.5 0 1 3.5-1.8 1.2c.8 1.8 2.1 3.1 3.9 3.9L10.3 8.3l3.7 1v2.5c0 1-1 1.9-2 1.7C6.6 12.8 2.9 9.1 2.1 3.6 1.9 2.5 2.5 1.5 3.5 1.5z"/></svg></span>
        <span>044-987 654 321</span>
      </li>
      <li class="contact-item">
        <span class="contact-icon"><svg viewBox="0 0 16 16"><path d="M1 3h14v10H1z"/><path d="M2 4l6 5 6-5" fill="none" stroke="#fff" stroke-width="1.2"/></svg></span>
        <span>info@quintelpack.com</span>
      </li>
      <li class="contact-item">
        <span class="contact-icon"><svg viewBox="0 0 16 16"><path d="M8 1a7 7 0 1 0 0 14A7 7 0 0 0 8 1z"/><path d="M1.5 8h13M8 1.5c2 2 2 11 0 13M8 1.5c-2 2-2 11 0 13" fill="none" stroke="#fff" stroke-width="1"/></svg></span>
        <span>www.quintelpack.com</span>
      </li>
      <li class="contact-item">
        <span class="contact-icon"><svg viewBox="0 0 16 16"><path d="M8 1a5 5 0 0 0-5 5c0 3.8 5 9 5 9s5-5.2 5-9a5 5 0 0 0-5-5zm0 7a2 2 0 1 1 0-4 2 2 0 0 1 0 4z"/></svg></span>
        <span>88, Harbor Road Suite 12<br>45810, Ashford Bay</span>
      </li>
    </ul>
  </section>
</main>
</body>
</html>
```